CAMBRAI CELEBRATES ANDOUILETTE

On the occasion of the big annual sale, in CAMBRAI, the 57th celebrates the Cambrai specialty "andouillette de CAMBRAI".

On this occasion, we are developing a special menu for this day;

- Authentic CAMBRAI sausage, old-fashioned mustard sauce, served with fresh fries cooked in beef fat and green salad
- CAMBRAI andouillette salad (lettuce, tomatoes, onions, CAMBRAI andouillette, Tome de CAMBRAI, Cambrai apples
- Andouillette gratin (Homemade mash, CAMBRAI andouillette, old-fashioned mustard, gratin with CAMBRAI tome
- BRUSCHETTA: Cream base, CAMBRAI sausage, CAMBRAI tome, onions, old-fashioned mustard
- Grilled ham
- Fried mussels, with CAMBRAI tome cream

The event will take place on Sunday July 2, in continuous service.

Please write in French, and insert the logo of the establishment of 57 and illustrate well.

THANKS

```html
<!DOCTYPE html>
<html lang="fr">
<head>
<meta charset="utf-8">
<title>La Table Dorée – Andouillette de Cambrai</title>
<link rel="stylesheet" href="https://fonts.googleapis.com/css2?family=Cinzel:wght@600;700&family=Playfair+Display:wght@700&family=Poppins:wght@400;500;600;700&display=swap">
<style>
  :root {
    --page-bg: #ececec;
    --slate: #262626;
    --slate-light: #3a3a3a;
    --wood: #f6f6f4;
    --wood-shade: #e6e6e3;
    --gold: #b07a22;
    --gold-light: #d9a441;
    --orange: #f29a17;
    --ink: #1a1a1a;
    --white: #ffffff;
  }
  * { margin: 0; padding: 0; box-sizing: border-box; }
  html, body { width: 1200px; height: 2400px; overflow: hidden; background: var(--page-bg); }
  .flyer {
    position: absolute; left: 0; top: 349px; width: 1200px; height: 1702px; overflow: hidden;
    background: linear-gradient(90deg, var(--wood) 0%, var(--wood-shade) 30%, var(--wood) 55%, var(--wood-shade) 80%, var(--wood) 100%);
    box-shadow: 0 10px 30px rgba(0,0,0,.25);
    font-family: "Poppins", sans-serif; color: var(--ink);
  }
  .slate-band {
    position: absolute; left: 0; top: 0; width: 1200px; height: 930px;
    background: radial-gradient(ellipse at 50% 30%, var(--slate-light), var(--slate) 70%);
  }
  .herb-garnish {
    position: absolute; right: 0; top: 0; width: 260px; height: 150px;
    background: radial-gradient(ellipse at 80% 20%, #4e6b3a, rgba(40,60,30,0) 70%);
  }
  .occasion {
    position: absolute; top: 68px; width: 100%; text-align: center;
    color: var(--white); font-size: 22px; font-weight: 400; letter-spacing: .3px;
  }
  .brand {
    position: absolute; top: 180px; width: 100%; display: flex; justify-content: center; align-items: center; gap: 16px;
    color: var(--white); font-size: 60px; font-weight: 600; line-height: 1;
  }
  .brand-dot { width: 20px; height: 20px; border-radius: 50%; background: var(--gold-light); }
  .tagline {
    position: absolute; top: 322px; width: 100%; text-align: center;
    color: var(--white); font-size: 27px; font-weight: 500; letter-spacing: 6px;
  }
  .title-small {
    position: absolute; top: 368px; width: 100%; text-align: center;
    font-family: "Cinzel", serif; font-weight: 700; color: var(--white); font-size: 46px; letter-spacing: 10px;
  }
  .title-main {
    position: absolute; top: 405px; width: 100%; text-align: center;
    font-family: "Cinzel", serif; font-weight: 700; font-size: 132px; line-height: 1.1;
    background: linear-gradient(180deg, var(--gold-light), var(--gold) 60%, #8a5b16);
    -webkit-background-clip: text; background-clip: text; color: transparent;
  }
  .dish-ring { position: absolute; border-radius: 50%; background: var(--orange); }
  .dish { position: absolute; border-radius: 50%; border: 14px solid #151515; }
  .dish-mussels { left: -40px; top: 575px; width: 430px; height: 430px;
    background: radial-gradient(circle at 45% 45%, #3b3f4a, #1c1f28 60%, #e9e9e9 64%); border-color: #eef1f6; }
  .dish-skillet { left: 372px; top: 593px; width: 470px; height: 470px;
    background: radial-gradient(circle at 50% 45%, #e2a13a, #c0512c 55%, #7a2a18 80%); }
  .dish-vegetables { left: 815px; top: 532px; width: 430px; height: 430px;
    background: radial-gradient(circle at 50% 50%, #f0b53a, #d9642c 50%, #8b4a2c 80%); }
  .veg-garnish {
    position: absolute; left: 870px; top: 1000px; width: 330px; height: 160px;
    background: radial-gradient(ellipse at 50% 50%, rgba(190,70,50,.25), rgba(120,140,60,0) 70%);
  }
  .menu-head { position: absolute; left: 61px; top: 1040px; }
  .menu-head .lead { font-family: "Cinzel", serif; font-weight: 700; color: var(--gold); font-size: 46px; line-height: 1; }
  .menu-head .sub { font-family: "Cinzel", serif; font-weight: 600; color: var(--ink); font-size: 36px; line-height: 1.2; }
  .menu-list { position: absolute; left: 61px; top: 1150px; width: 470px; list-style: none; }
  .menu-item { position: relative; padding-left: 27px; margin-bottom: 22px; }
  .menu-item svg { position: absolute; left: 0; top: 9px; }
  .dish-name { color: var(--gold); font-size: 22px; font-weight: 700; line-height: 1.25; }
  .dish-desc { font-size: 18px; line-height: 1.2; }
  .date-box {
    position: absolute; left: 632px; top: 1180px; width: 501px; height: 207px;
    border: 3px solid var(--ink);
  }
  .date-day {
    position: absolute; left: 28px; top: -22px; font-family: "Playfair Display", serif; font-weight: 700;
    font-size: 230px; line-height: 1; color: var(--gold); font-variant-numeric: lining-nums;
  }
  .date-month {
    position: absolute; left: 180px; top: 14px; font-family: "Playfair Display", serif; font-weight: 700;
    font-size: 74px; line-height: 1; letter-spacing: 1px;
  }
  .date-weekday {
    position: absolute; left: 180px; top: 96px; width: 292px; height: 86px; background: var(--ink); color: var(--white);
    font-family: "Playfair Display", serif; font-weight: 700; font-size: 44px; line-height: 60px; text-align: center; letter-spacing: 1px;
  }
  .service { position: absolute; left: 632px; top: 1392px; font-size: 48px; font-weight: 500; }
  .divider { position: absolute; left: 632px; top: 1491px; width: 501px; border-top: 2px dashed var(--gold); }
  .follow { position: absolute; left: 632px; top: 1532px; font-size: 27px; }
  .social { position: absolute; left: 634px; top: 1585px; display: flex; align-items: center; gap: 22px; font-size: 34px; font-weight: 700; }
  .social-square { width: 44px; height: 44px; background: var(--gold); }
</style>
</head>
<body>
  <main class="flyer">
    <div class="slate-band"></div>
    <div class="herb-garnish" role="img" aria-label="Brins de romarin frais"></div>

    <p class="occasion">A L’OCCASION DE LA GRANDE VENTE ANNUELLE, À CAMBRAI</p>
    <div class="brand"><span class="brand-dot"></span><span>La Table Dorée</span></div>

    <p class="tagline">CÉLÈBRE LA SPÉCIALITÉ CAMBRAÏENNE</p>
    <h1 class="title-small">ANDOUILLETTE DE</h1>
    <h2 class="title-main">CAMBRAI</h2>

    <div class="dish-ring" style="left:-20px;top:560px;width:450px;height:450px;"></div>
    <div class="dish-ring" style="left:350px;top:575px;width:520px;height:520px;"></div>
    <div class="dish-ring" style="left:800px;top:505px;width:460px;height:460px;"></div>
    <div class="dish dish-mussels" role="img" aria-label="Assiette de moules au citron avec pain grillé"></div>
    <div class="dish dish-vegetables" role="img" aria-label="Poêlée de saucisse et légumes colorés"></div>
    <div class="dish dish-skillet" role="img" aria-label="Poêlon en fonte d’andouillette de Cambrai et frites"></div>
    <div class="veg-garnish" role="img" aria-label="Tomates cerises, olives, oignon et piment éparpillés"></div>

    <div class="menu-head">
      <p class="lead">MENU SPÉCIAL</p>
      <p class="sub">POUR CETTE JOURNÉE</p>
    </div>

    <ul class="menu-list">
      <li class="menu-item">
        <svg width="14" height="14" viewBox="0 0 14 14"><circle cx="7" cy="7" r="7" fill="#1a1a1a"/><path d="M3.5 7.2l2.3 2.2 4.6-4.6" stroke="#fff" stroke-width="1.8" fill="none"/></svg>
        <p class="dish-name">SAUCISSE CAMBRAI AUTHENTIQUE</p>
        <p class="dish-desc">authentique, sauce à la moutarde à l’ancienne, servie avec des frites fraîches cuites dans de la graisse de bœuf et de la salade verte</p>
      </li>
      <li class="menu-item">
        <svg width="14" height="14" viewBox="0 0 14 14"><circle cx="7" cy="7" r="7" fill="#1a1a1a"/><path d="M3.5 7.2l2.3 2.2 4.6-4.6" stroke="#fff" stroke-width="1.8" fill="none"/></svg>
        <p class="dish-name">SALADE D’ANDOUILLETTE CAMBRAI</p>
        <p class="dish-desc">laitue, tomates, oignons, andouillette CAMBRAI, Tome de CAMBRAI, pommes Cambrai</p>
      </li>
      <li class="menu-item">
        <svg width="14" height="14" viewBox="0 0 14 14"><circle cx="7" cy="7" r="7" fill="#1a1a1a"/><path d="M3.5 7.2l2.3 2.2 4.6-4.6" stroke="#fff" stroke-width="1.8" fill="none"/></svg>
        <p class="dish-name">GRATIN D’ANDOUILLETTE</p>
        <p class="dish-desc">purée maison, andouillette CAMBRAI, moutarde à l’ancienne, gratin au tome CAMBRAI</p>
      </li>
      <li class="menu-item">
        <svg width="14" height="14" viewBox="0 0 14 14"><circle cx="7" cy="7" r="7" fill="#1a1a1a"/><path d="M3.5 7.2l2.3 2.2 4.6-4.6" stroke="#fff" stroke-width="1.8" fill="none"/></svg>
        <p class="dish-name">BRUSCHETTA</p>
        <p class="dish-desc">Base crème, saucisse CAMBRAI, tome CAMBRAI, oignons, moutarde à l’ancienne</p>
      </li>
      <li class="menu-item">
        <svg width="14" height="14" viewBox="0 0 14 14"><circle cx="7" cy="7" r="7" fill="#1a1a1a"/><path d="M3.5 7.2l2.3 2.2 4.6-4.6" stroke="#fff" stroke-width="1.8" fill="none"/></svg>
        <p class="dish-name">JAMBON GRILLÉ</p>
      </li>
      <li class="menu-item">
        <svg width="14" height="14" viewBox="0 0 14 14"><circle cx="7" cy="7" r="7" fill="#1a1a1a"/><path d="M3.5 7.2l2.3 2.2 4.6-4.6" stroke="#fff" stroke-width="1.8" fill="none"/></svg>
        <p class="dish-name">MOULES FRITES</p>
        <p class="dish-desc">à la crème tome CAMBRAI</p>
      </li>
    </ul>

    <div class="date-box">
      <span class="date-day">2</span>
      <span class="date-month">JUILLET</span>
      <span class="date-weekday">DIMANCHE</span>
    </div>
    <p class="service">EN SERVICE CONTINU</p>
    <div class="divider"></div>
    <p class="follow">Follow us on</p>
    <div class="social"><span class="social-square"></span><span>@La Table Dorée Cambrai</span></div>
  </main>
</body>
</html>
```